Business Card Design for ReaL ESTATE AGENT

New Business Cards for a real estate agent in Jacksonville, FL. My specialty is urban core, historic districts but sell through out the city. Company Name is Ninth and Crest Realty a division of the Dunholt Companies. The card needs to convey an essence of professionalism, knowledge and success.

Target Market(s)

Home buyers and Sellers

Industry/Entity Type

Real Estate

Contact Information for Business Card

Double sided

Font styles to use
Sans Serif

Requirements
Must have
• My logs and photo (provided). My contact information as follows:
• Owen Talbrick
• Cell 904-555-0183
• Office 904-555-0147
• Email owentalbrick@mailbrook.example
Nice to have
• Tag Line - Exceptional Effort. Proven Results.

```html
<!DOCTYPE html>
<html lang="en">
<head>
<meta charset="utf-8">
<title>Ninth and Crest Realty – Business Card</title>
<link rel="stylesheet" href="https://fonts.googleapis.com/css2?family=Source+Sans+3:wght@400;600;700&display=swap">
<style>
  :root {
    --backdrop: #e9e7e4;
    --card: #ffffff;
    --brand-green: #1f5e45;
    --brand-orange: #ee5840;
    --ink: #2e2e2e;
    --photo-light: #c9c3bd;
    --photo-dark: #3b3d42;
  }
  * { margin: 0; padding: 0; box-sizing: border-box; }
  html, body {
    width: 1200px; height: 900px; overflow: hidden;
    background: var(--backdrop);
    font-family: "Source Sans 3", "Helvetica Neue", Arial, sans-serif;
  }
  .stage { position: relative; width: 1200px; height: 900px; }
  .card {
    position: absolute;
    background: var(--card);
    box-shadow: 0 4px 14px rgba(0,0,0,0.12);
    overflow: hidden;
  }
  .card--front { left: 238px; top: 62px; width: 555px; height: 342px; }
  .card--back { left: 457px; top: 518px; width: 560px; height: 344px; }

  .agent-photo {
    position: absolute; left: 2px; top: 35px; width: 208px; height: 252px;
    background: linear-gradient(180deg, var(--photo-light) 0%, #b49a8a 45%, var(--photo-dark) 100%);
  }
  .agent-info { position: absolute; left: 322px; top: 100px; color: var(--ink); }
  .agent-name { font-size: 19px; font-weight: 600; color: var(--brand-green); line-height: 22px; }
  .agent-title { font-size: 15px; line-height: 18px; margin-top: 1px; }
  .contact-list { list-style: none; margin-top: 36px; font-size: 14px; line-height: 20px; }
  .contact-list li { display: flex; align-items: center; gap: 6px; white-space: nowrap; }
  .contact-list svg { width: 11px; height: 11px; fill: var(--brand-green); flex: none; }

  .stripe { position: absolute; left: 0; width: 100%; }
  .stripe--arrow { top: 278px; height: 35px; }
  .stripe--orange { top: 304px; height: 38px; background: var(--brand-orange); }

  .brand-mark {
    position: absolute; inset: 0;
    display: flex; align-items: center; justify-content: center; gap: 12px;
  }
  .brand-square { width: 26px; height: 26px; background: var(--brand-green); }
  .brand-name { font-size: 30px; font-weight: 700; color: var(--brand-orange); letter-spacing: 0.5px; }
</style>
</head>
<body>
<main class="stage">
  <section class="card card--front" aria-label="Card front">
    <div class="agent-photo" role="img" aria-label="Portrait photo of the agent in a dark suit and red tie"></div>
    <div class="agent-info">
      <p class="agent-name">Owen Talbrick</p>
      <p class="agent-title">Managing Director</p>
      <ul class="contact-list">
        <li>
          <svg viewBox="0 0 24 24" aria-hidden="true"><path d="M6.6 10.8a15.1 15.1 0 0 0 6.6 6.6l2.2-2.2a1 1 0 0 1 1-.25 11.4 11.4 0 0 0 3.6.57 1 1 0 0 1 1 1V20a1 1 0 0 1-1 1A17 17 0 0 1 3 4a1 1 0 0 1 1-1h3.5a1 1 0 0 1 1 1c0 1.25.2 2.45.57 3.6a1 1 0 0 1-.25 1z"/></svg>
          Cell 904-555-0183
        </li>
        <li>
          <svg viewBox="0 0 24 24" aria-hidden="true"><path d="M6.6 10.8a15.1 15.1 0 0 0 6.6 6.6l2.2-2.2a1 1 0 0 1 1-.25 11.4 11.4 0 0 0 3.6.57 1 1 0 0 1 1 1V20a1 1 0 0 1-1 1A17 17 0 0 1 3 4a1 1 0 0 1 1-1h3.5a1 1 0 0 1 1 1c0 1.25.2 2.45.57 3.6a1 1 0 0 1-.25 1z"/></svg>
          Office 904-555-0147
        </li>
        <li>
          <svg viewBox="0 0 24 24" aria-hidden="true"><path d="M2 5h20v14H2z M2 5l10 8 10-8" /></svg>
          owentalbrick@mailbrook.example
        </li>
      </ul>
    </div>
    <div class="stripe stripe--orange"></div>
    <svg class="stripe stripe--arrow" viewBox="0 0 555 35" preserveAspectRatio="none" aria-hidden="true">
      <polygon points="0,9 530,9 530,0 555,17.5 530,35 530,26 0,26" fill="var(--brand-green)"/>
    </svg>
  </section>

  <section class="card card--back" aria-label="Card back">
    <div class="brand-mark">
      <span class="brand-square" aria-hidden="true"></span>
      <span class="brand-name">Ninth and Crest Realty</span>
    </div>
  </section>
</main>
</body>
</html>
```